Custom Manufacturing Company square space website design

I own a custom manufacturing company that uses precision cutting technology to manufacture project components over a couple industries. We have an industrial CNC router and state of the art edge bander and cut a lot of cabinetry components for cabinet shops, builders, closet companies, ect. We offer design and assembly for any cabinetry or can build cabinets to spec. We also cut components for other industries out of wood, plastics, acryclics, ect. We offer design engineering services, product development protype services. we have a 3D printer farm. We want our communicate trust, dependability, and the value we place on client relationships.

We essentially want a credibility website. Landing page and drops downs for services we offer, capabilites, about us, contact

```html
<!DOCTYPE html>
<html lang="en">
<head>
<meta charset="utf-8">
<title>Northfield CNC</title>
<link href="https://fonts.googleapis.com/css2?family=Syncopate:wght@400;700&family=Montserrat:ital,wght@0,400;0,500;0,600;0,700;1,400;1,500&family=Roboto:wght@400;500;700&display=swap" rel="stylesheet">
<style>
:root{
  --orange:#f99d45;
  --orange-soft:#fbd9b8;
  --cream:#fcf1e6;
  --ink:#111111;
  --text:#333333;
  --white:#ffffff;
  --footer:#000000;
}
*{margin:0;padding:0;box-sizing:border-box}
html,body{width:1200px;height:3482px;overflow:hidden}
body{position:relative;font-family:"Montserrat",sans-serif;color:var(--text);background:var(--white)}
.abs{position:absolute}
.display{font-family:"Syncopate",sans-serif;font-weight:700;color:var(--ink);letter-spacing:3px}
.rule{position:absolute;height:4px;width:76px;background:var(--ink);border-radius:50%}
.btn{position:absolute;background:var(--orange);color:var(--white);font-weight:700;font-size:19px;display:flex;align-items:center;justify-content:center;border-radius:24px 6px 24px 6px}

/* hero */
.hero{left:0;top:0;width:1200px;height:562px;background:linear-gradient(100deg,#efedeb 0%,#f4f2ef 35%,#e2ddd6 60%,#cfc6bc 85%,#7b6a5d 100%)}
.brand{left:111px;top:14px;width:210px;text-align:center}
.brand-mark{width:56px;height:56px;border:3px solid var(--ink);margin:0 auto 10px}
.brand-name{font-family:"Syncopate",sans-serif;font-weight:700;font-size:20px;color:var(--ink);letter-spacing:3px;white-space:nowrap}
.nav{top:32px;font-size:16px;font-weight:500;color:var(--ink)}
.hero-welcome{left:113px;top:178px;font-size:21px;font-weight:500;color:var(--ink)}
.hero-title{left:113px;top:214px;font-size:34px;white-space:nowrap}
.hero-text{left:113px;top:279px;width:340px;font-size:16px;line-height:26px;color:var(--ink)}

/* about */
.about{left:0;top:570px;width:1200px;height:646px;background:linear-gradient(180deg,#f2f1ef 0%,#ecebe8 70%,#d8d3cc 100%)}
.about-media{left:30px;top:650px;width:1030px;height:540px;background:radial-gradient(ellipse at 20% 45%,#4f6a3a 0%,rgba(79,106,58,0) 28%),radial-gradient(ellipse at 60% 78%,#e2cba6 0%,rgba(226,203,166,0) 45%)}
.about-title{left:647px;top:648px;font-size:32px}
.about-text{left:647px;top:732px;width:425px;font-size:14px;line-height:23px;color:var(--ink)}

/* services */
.section-title{font-size:32px;text-align:center;width:1200px;left:0}
.card-back{position:absolute;width:173px;height:269px;background:var(--orange-soft);border-radius:26px 12px 12px 0}
.card-back.active{background:var(--orange)}
.card-photo{position:absolute;width:184px;height:271px}
.card-num{position:absolute;width:40px;height:37px;background:var(--orange);color:var(--white);font-size:13px;display:flex;align-items:center;justify-content:center;letter-spacing:2px}
.card-tag{position:absolute;writing-mode:vertical-rl;font-family:"Syncopate",sans-serif;font-weight:700;font-size:13px;letter-spacing:2px;color:var(--ink)}
.card-title{position:absolute;width:240px;text-align:center;font-size:18px;font-weight:600;color:var(--ink);line-height:26px}
.card-text{position:absolute;width:240px;text-align:center;font-size:15px;line-height:23px;color:var(--ink)}
.arrow-dark{position:absolute;width:26px;height:26px;border-radius:50%;background:var(--ink)}

/* testimonials */
.testimonials{left:0;top:1946px;width:1200px;height:389px;background:linear-gradient(90deg,var(--orange) 0%,var(--orange) 55%,#f3a45a 100%)}
.testi-title{color:var(--white)}
.testi-photo{left:242px;top:2118px;width:138px;height:136px;border-radius:12px;background:linear-gradient(160deg,#c9c2b4,#8c8478)}
.testi-name{left:438px;top:2097px;font-size:18px;font-weight:700;color:var(--white)}
.testi-text{left:438px;top:2136px;width:615px;font-size:16px;line-height:23px;color:var(--white)}
.testi-quote{left:442px;top:2246px;font-size:16px;font-style:italic;color:var(--white)}
.arrow-light{position:absolute;width:26px;height:26px;border-radius:50%;border:2px solid var(--white)}

/* contact */
.contact-bg{left:0;top:2335px;width:1200px;height:765px;background:linear-gradient(180deg,#ffffff 0%,#f4f4f4 18%,#dcdcdc 60%,#8d8c8a 100%)}
.watermark{left:1040px;top:2443px;font-family:"Syncopate",sans-serif;font-weight:700;font-size:14px;letter-spacing:2px;color:#d4d4d4}
.form-card{left:162px;top:2524px;width:877px;height:494px;background:var(--white);box-shadow:0 0 18px rgba(0,0,0,.12)}
.label{position:absolute;font-size:15px;color:var(--ink);letter-spacing:.3px}
.field{position:absolute;background:var(--cream);border:1px solid #ece3d8;font-size:14px;font-style:italic;font-weight:500;color:var(--ink);padding-left:23px;display:flex;align-items:center}
.field.area{align-items:flex-start;padding-top:16px}

/* footer */
.footer{left:0;top:3100px;width:1200px;height:382px;background:var(--footer);color:var(--white);font-family:"Roboto",sans-serif}
.f-brand .brand-mark{border-color:var(--white);width:60px;height:60px}
.f-brand .brand-name{color:var(--white)}
.f-head{position:absolute;font-size:17px;font-weight:700}
.f-list{position:absolute;list-style:none;font-size:16px;font-weight:500;line-height:31px}
.social{position:absolute;width:26px;height:26px;border-radius:50%;background:var(--white)}
</style>
</head>
<body>

<!-- HERO -->
<div class="abs hero" role="img" aria-label="Bright bedroom with white cabinetry, shelving, a desk and a window"></div>
<div class="abs brand">
  <div class="brand-mark"></div>
  <div class="brand-name">NORTHFIELD CNC</div>
</div>
<div class="abs nav" style="left:405px">Home</div>
<div class="abs nav" style="left:489px">Services We Offer ▾</div>
<div class="abs nav" style="left:677px">Capabilities</div>
<div class="abs nav" style="left:811px">About Us</div>
<div class="abs nav" style="left:919px">Contact</div>
<svg class="abs" style="left:1020px;top:34px" width="16" height="16" viewBox="0 0 16 16"><circle cx="6.5" cy="6.5" r="4.5" fill="none" stroke="#111" stroke-width="2.2"/><line x1="10" y1="10" x2="14.5" y2="14.5" stroke="#111" stroke-width="2.5"/></svg>
<svg class="abs" style="left:1070px;top:34px" width="17" height="16" viewBox="0 0 17 16"><path d="M1 2h3l2 8h8l2-6H5" fill="none" stroke="#111" stroke-width="2"/><circle cx="7" cy="13.5" r="1.5" fill="#111"/><circle cx="13" cy="13.5" r="1.5" fill="#111"/></svg>
<div class="abs hero-welcome">Welcome</div>
<div class="abs display hero-title">Northfield CNC</div>
<p class="abs hero-text">Lorem ipsum dolor sit amet, consectetur adipiscing elit, sed do.</p>
<div class="btn" style="left:113px;top:361px;width:180px;height:43px">Get Started</div>

<!-- ABOUT -->
<div class="abs about"></div>
<div class="abs about-media" role="img" aria-label="Potted plant beside a light wood media console with white drawers"></div>
<h2 class="abs display about-title">About Us</h2>
<div class="rule" style="left:647px;top:690px"></div>
<p class="abs about-text">Lorem ipsum dolor sit amet, consectetur adipiscing elit, sed do eiusmod tempor incididunt ut labore et dolore magna aliqua. Ut enim ad minim veniam, quis nostrud exercitation ullamco laboris nisi ut aliquip ex ea commodo consequat. Duis aute irure dolor in reprehenderit in voluptate velit esse cillum dolore eu fugiat nulla pariatur.</p>
<div class="btn" style="left:649px;top:923px;width:178px;height:45px">Read More</div>

<!-- SERVICES -->
<h2 class="abs display section-title" style="top:1298px">Services We Offer</h2>
<div class="rule" style="left:380px;top:1343px"></div>
<div class="arrow-dark" style="left:46px;top:1553px"></div>
<svg class="abs" style="left:53px;top:1559px" width="12" height="14" viewBox="0 0 12 14"><path d="M8 2L3 7l5 5" fill="none" stroke="#fff" stroke-width="2.5"/></svg>
<div class="arrow-dark" style="left:1127px;top:1553px"></div>
<svg class="abs" style="left:1134px;top:1559px" width="12" height="14" viewBox="0 0 12 14"><path d="M4 2l5 5-5 5" fill="none" stroke="#fff" stroke-width="2.5"/></svg>

<div class="card-back" style="left:157px;top:1407px"></div>
<div class="card-photo" role="img" aria-label="Engineer reviewing drawings at a workbench" style="left:116px;top:1432px;background:linear-gradient(160deg,#d9cdb6,#b98f5a 55%,#6f6252)"></div>
<div class="card-num" style="left:116px;top:1432px">01</div>
<div class="card-tag" style="left:304px;top:1443px">LORUM IPSUM STYLE</div>
<div class="card-title" style="left:90px;top:1726px">Design Engineering</div>
<div class="card-text" style="left:89px;top:1785px">Sed ut perspiciatis unde omnis iste natus error sit voluptatem</div>

<div class="card-back active" style="left:411px;top:1407px"></div>
<div class="card-photo" role="img" aria-label="Installer fitting white cabinetry from a ladder" style="left:370px;top:1432px;background:linear-gradient(160deg,#f1f1ef,#d7d5d0 60%,#8f8a80)"></div>
<div class="card-num" style="left:370px;top:1432px">02</div>
<div class="card-tag" style="left:558px;top:1443px">LORUM IPSUM STYLE</div>
<div class="card-title" style="left:344px;top:1726px">Product Development Prototype</div>
<div class="card-text" style="left:343px;top:1785px">Sed ut perspiciatis unde omnis iste natus error sit voluptatem</div>

<div class="card-back" style="left:664px;top:1407px"></div>
<div class="card-photo" role="img" aria-label="3D printer nozzle extruding a part" style="left:623px;top:1432px;background:linear-gradient(160deg,#3a6fb0,#9aa3ad 55%,#5d5c5a)"></div>
<div class="card-num" style="left:623px;top:1432px">03</div>
<div class="card-tag" style="left:811px;top:1443px">LORUM IPSUM STYLE</div>
<div class="card-title" style="left:597px;top:1726px">3D Printer Farm</div>
<div class="card-text" style="left:596px;top:1785px">Sed ut perspiciatis unde omnis iste natus error sit voluptatem</div>

<div class="card-back" style="left:918px;top:1407px"></div>
<div class="card-photo" role="img" aria-label="Worker cutting wood components with a saw" style="left:877px;top:1432px;background:linear-gradient(160deg,#4a3a2e,#a8622e 55%,#d9b48a)"></div>
<div class="card-num" style="left:877px;top:1432px">04</div>
<div class="card-tag" style="left:1065px;top:1443px">LORUM IPSUM STYLE</div>
<div class="card-title" style="left:850px;top:1726px">Cut Components<br>For Other</div>
<div class="card-text" style="left:850px;top:1785px">Sed ut perspiciatis unde omnis iste natus error sit voluptatem</div>

<!-- TESTIMONIALS -->
<div class="abs testimonials"></div>
<h2 class="abs display section-title testi-title" style="top:1994px">Testimonials</h2>
<div class="rule" style="left:447px;top:2037px;background:var(--white)"></div>
<div class="arrow-light" style="left:46px;top:2141px"></div>
<svg class="abs" style="left:53px;top:2147px" width="12" height="14" viewBox="0 0 12 14"><path d="M8 2L3 7l5 5" fill="none" stroke="#fff" stroke-width="2.5"/></svg>
<div class="arrow-light" style="left:1127px;top:2141px"></div>
<svg class="abs" style="left:1134px;top:2147px" width="12" height="14" viewBox="0 0 12 14"><path d="M4 2l5 5-5 5" fill="none" stroke="#fff" stroke-width="2.5"/></svg>
<div class="abs testi-photo" role="img" aria-label="Portrait of the client"></div>
<div class="abs testi-name">J. Marlow</div>
<p class="abs testi-text">Lorem ipsum dolor sit amet, consectetur adipiscing elit, sed do eiusmod tempor incididunt ut labore et dolore magna aliqua. Ut enim ad minim veniam, quis nostrud exercitation ullamco laboris nisi ut aliquip ex ea commodo consequat. Duis aute irure dolor in reprehenderit in voluptate.</p>
<div class="abs testi-quote">( consequuntur magni dolores eos qui ratione voluptatem )</div>

<!-- CONTACT -->
<div class="abs contact-bg" role="img" aria-label="White closet and drawer cabinetry in a room"></div>
<h2 class="abs display section-title" style="top:2423px">Contact Us</h2>
<div class="rule" style="left:465px;top:2468px"></div>
<div class="abs watermark">NORTHFIELD<br>CNC</div>
<div class="abs form-card"></div>
<div class="label" style="left:216px;top:2568px">FIRST NAME *</div>
<div class="label" style="left:653px;top:2568px">LAST NAME *</div>
<div class="field" style="left:216px;top:2601px;width:326px;height:50px">Ellis</div>
<div class="field" style="left:653px;top:2601px;width:326px;height:50px">Varner</div>
<div class="label" style="left:216px;top:2667px">PHONE *</div>
<div class="label" style="left:653px;top:2667px">E MAIL</div>
<div class="field" style="left:216px;top:2700px;width:326px;height:50px">555-201-4477</div>
<div class="field" style="left:653px;top:2700px;width:326px;height:50px">info@ellisvarner.com</div>
<div class="label" style="left:216px;top:2768px">MESSAGE</div>
<div class="field area" style="left:216px;top:2801px;width:763px;height:73px">Describe Your ...</div>
<div class="btn" style="left:511px;top:2901px;width:178px;height:45px">Submit</div>

<!-- FOOTER -->
<div class="abs footer"></div>
<div class="abs brand f-brand" style="left:118px;top:3126px;width:226px">
  <div class="brand-mark"></div>
  <div class="brand-name">NORTHFIELD CNC</div>
</div>
<div class="abs" style="left:119px;top:3282px;font-family:Roboto,sans-serif;font-size:16px;font-weight:500;color:#fff">Follow Us</div>
<div class="social" style="left:233px;top:3278px" role="img" aria-label="Social profile"></div>
<div class="social" style="left:275px;top:3278px" role="img" aria-label="Social profile"></div>
<div class="social" style="left:315px;top:3278px" role="img" aria-label="Social profile"></div>
<svg class="abs" style="left:128px;top:3345px" width="28" height="20" viewBox="0 0 28 20"><rect x="1" y="1" width="26" height="18" fill="none" stroke="#fff" stroke-width="2"/><path d="M1 1l13 11L27 1M1 19l10-9M27 19l-10-9" fill="none" stroke="#fff" stroke-width="2"/></svg>
<div class="abs" style="left:178px;top:3344px;font-family:Roboto,sans-serif;font-size:16px;font-weight:500;color:#fff">info@northfieldcnc.com</div>
<svg class="abs" style="left:129px;top:3384px" width="26" height="26" viewBox="0 0 26 26"><path d="M6 3l4 5-2.5 2.5c1.5 3 4 5.5 7 7L17 15l5 4-2.5 4C11 22 4 15 3 6z" fill="#fff"/><path d="M15 3a8 8 0 0 1 8 8M15 7a4 4 0 0 1 4 4" fill="none" stroke="#fff" stroke-width="1.8"/></svg>
<div class="abs" style="left:178px;top:3386px;font-family:Roboto,sans-serif;font-size:16px;font-weight:500;color:#fff">+1 (555) 0142 555</div>

<div class="f-head" style="left:454px;top:3197px;color:#fff">Our Links</div>
<ul class="f-list" style="left:454px;top:3234px;color:#fff"><li>Home</li><li>Services we offer</li><li>Capabilities</li><li>About us</li><li>Contact</li></ul>
<div class="f-head" style="left:685px;top:3197px;color:#fff">Other Links</div>
<ul class="f-list" style="left:685px;top:3234px;color:#fff"><li>FAQ</li><li>Offer</li><li>Testimonial</li><li>Location</li></ul>
<div class="f-head" style="left:888px;top:3197px;color:#fff">Our&nbsp; Address</div>
<ul class="f-list" style="left:888px;top:3234px;color:#fff"><li>Lorem ipsum dolor sit amet,</li><li>Sed ut perspiciatis,</li><li>Molestiae consequatur,</li><li>Est laborum.</li></ul>
<div class="abs" style="left:697px;top:3408px;font-family:Roboto,sans-serif;font-size:16px;font-weight:500;color:#fff">Copyright2023@NORTHFIELD CNC. All Rights Reserved</div>

</body>
</html>
```